Award-winnning Estate Agent needs a premium version of their 'For Sale' board design

We need a premium option for our 'For Sale' board design. We have a standard board that is attached to this brief, but were are looking to have a premium design version that we will use when selling exclusive properties. Our company name is Harbourline Vale Estates and the name for this is exclusive selection is: 'The Harbourline Collection'. The design needs to work with our current brand, but have a distinctive PREMIUM feel to it. I have uploaded the barnd guidelines and also some of the exisisting logo variations. We do NOT need a new logo but feel free to play around with colours, fonts, sizes etc. for the sign.

Target Market(s)

Property buyers & house hunters

Industry/Entity Type

Real Estate - Residential Property

Font styles to use
Sans Serif

Requirements
Must have
• A premium fee, must be square design, must be easy to read when driving past the sign
Nice to have
• I'm open ot ideas

```html
<!DOCTYPE html>
<html lang="en">
<head>
<meta charset="utf-8">
<title>For Sale Board – The Harbourline Collection</title>
<link href="https://fonts.googleapis.com/css2?family=Montserrat:wght@300;400;600;700&family=Inter:wght@600&display=swap" rel="stylesheet">
<style>
  :root {
    --board-dark: #363435;
    --panel-white: #ffffff;
    --brand-blue: #0b6db5;
    --accent-blue: #2ea8e0;
    --link-blue: #7fd3f7;
    --text-white: #ffffff;
  }
  html, body {
    margin: 0;
    padding: 0;
    width: 1200px;
    height: 1200px;
    overflow: hidden;
    background: var(--board-dark);
  }
  .sale-board {
    display: block;
    width: 1200px;
    height: 1200px;
  }
  .board-base { fill: var(--board-dark); }
  .header-panel { fill: var(--panel-white); }
  .header-stripe { fill: var(--accent-blue); }
  .header-hairline { fill: none; stroke: var(--panel-white); stroke-width: 1.2; }
  .headline {
    font-family: "Montserrat", sans-serif;
    font-weight: 700;
    font-size: 204px;
    fill: var(--brand-blue);
  }
  .brand-mark { fill: var(--accent-blue); }
  .collection-name {
    font-family: "Montserrat", sans-serif;
    font-weight: 300;
    font-size: 38px;
    fill: var(--text-white);
  }
  .collection-rule { stroke: var(--accent-blue); stroke-width: 2; }
  .brand-name {
    font-family: "Inter", sans-serif;
    font-weight: 600;
    font-size: 80px;
    fill: var(--accent-blue);
  }
  .phone-number {
    font-family: "Montserrat", sans-serif;
    font-weight: 700;
    font-size: 142px;
    fill: var(--text-white);
  }
  .web-address {
    font-family: "Montserrat", sans-serif;
    font-weight: 400;
    font-size: 44px;
    fill: var(--text-white);
  }
  .web-address .web-domain {
    font-weight: 600;
    fill: var(--link-blue);
  }
</style>
</head>
<body>
<svg class="sale-board" viewBox="0 0 1200 1200" xmlns="http://www.w3.org/2000/svg" role="img" aria-label="For Sale board for The Harbourline Collection by Harbourline Vale Estates">
  <rect class="board-base" x="0" y="0" width="1200" height="1200"/>

  <polygon class="header-stripe" points="0,0 1200,0 1200,257 601,451 0,257"/>
  <polygon class="header-panel" points="0,0 1200,0 1200,236 601,431 0,237"/>
  <polyline class="header-hairline" points="0,259 601,453 1200,259"/>

  <text class="headline" x="600" y="226" text-anchor="middle" textLength="990" lengthAdjust="spacingAndGlyphs">FOR SALE</text>

  <rect class="brand-mark" x="555" y="500" width="90" height="90"/>

  <text class="collection-name" x="600" y="680" text-anchor="middle" textLength="760" lengthAdjust="spacing">THE HARBOURLINE COLLECTION</text>
  <line class="collection-rule" x1="480" y1="722" x2="720" y2="722"/>

  <text class="brand-name" x="600" y="877" text-anchor="middle" textLength="920" lengthAdjust="spacingAndGlyphs">Harbourline Vale Estates</text>

  <text class="phone-number" x="600" y="1040" text-anchor="middle" textLength="895" lengthAdjust="spacingAndGlyphs">01632 960418</text>

  <text class="web-address" x="600" y="1101" text-anchor="middle" textLength="912" lengthAdjust="spacing">www.<tspan class="web-domain">harbourlinevaleestates</tspan>.co.uk</text>
</svg>
</body>
</html>
```